Oakmere Animal Care Group of Central Pennsylvania

I need a business card design for a new company in Harrisburg PA called "Animal Care Oakmere Group of Central PA". I will be providing relief services for veterinarians who need coverage during vacations; sick/maternity leave, etc. I would like to see the veterinarian symbol incorporated in the design in combination with animals (dogs /cats/birds/reptiles an pocket pets). Include My full name: Tomás R. Quintaval DVM, MLAS, BS. Also include my e mail (dvmtrq@mailbrook.net) and phone number 5552846017

Target Market(s)

Small Animal Veterinarian, practice owner

Industry/Entity Type

Business

Contact Information for Business Card

Oakmere Animal Care Group of Central PA

Font styles to use
Script

Requirements
Must have
• Veterinarian caduceus (see image) and Small animals (pets) within the logo.
Nice to have
• Give a sense of relaxation (vacationing)
Should not have
• Large animals, i.e. horses, cows, zoo animals...

```html
<!DOCTYPE html>
<html lang="en">
<head>
<meta charset="utf-8">
<title>Animal Care Oakmere Group of Central PA – Business Card</title>
<link rel="stylesheet" href="https://fonts.googleapis.com/css2?family=Marcellus+SC&family=Parisienne&family=PT+Serif&display=swap">
<style>
  :root {
    --page-bg: #e9e6e1;
    --card-white: #fbfbfa;
    --band-black: #0d0d0d;
    --accent-red: #c8323a;
    --ink: #1c1c1c;
    --band-text: #f4f4f4;
    --band-muted: #bdbdbd;
  }
  * { box-sizing: border-box; margin: 0; padding: 0; }
  html, body { width: 1200px; height: 892px; overflow: hidden; }
  body { background: var(--page-bg); position: relative; }

  .card {
    position: absolute;
    left: 100px; top: 166px;
    width: 1000px; height: 560px;
    background: var(--card-white);
    overflow: hidden;
    box-shadow: 0 6px 24px rgba(0,0,0,.18);
  }

  .brand {
    position: absolute;
    left: 0; right: 0; top: 100px;
    display: flex; align-items: center; justify-content: center; gap: 28px;
  }
  .brand-mark {
    width: 120px; height: 120px;
    border-radius: 50%;
    border: 6px solid var(--accent-red);
  }
  .brand-name {
    font-family: "Marcellus SC", serif;
    font-size: 34px; line-height: 1.2;
    color: var(--ink);
    letter-spacing: 1px;
  }

  .rule-top {
    position: absolute; left: 0; right: 0; top: 322px; height: 8px;
    background: var(--accent-red);
  }
  .band {
    position: absolute; left: 0; right: 0; top: 342px; height: 150px;
    background: var(--band-black);
    border-top: 5px solid var(--accent-red);
    border-bottom: 5px solid var(--accent-red);
    display: flex; align-items: center;
  }
  .holder {
    flex: 0 0 470px;
    padding-left: 60px;
    color: var(--band-text);
  }
  .holder-name {
    font-family: "Parisienne", cursive;
    font-size: 48px;
    line-height: 1.15;
    white-space: nowrap;
  }
  .holder-credentials {
    font-family: "PT Serif", serif;
    font-size: 19px;
    letter-spacing: 1px;
    color: var(--band-muted);
    padding-left: 6px;
    white-space: nowrap;
  }
  .band-divider {
    width: 2px; height: 80px;
    background: linear-gradient(to bottom, transparent, #888, transparent);
    transform: rotate(20deg);
    margin-right: 60px;
  }
  .contact { list-style: none; }
  .contact li {
    display: flex; align-items: center; gap: 22px;
    font-family: "PT Serif", serif;
    font-size: 27px;
    color: var(--band-text);
    line-height: 1.6;
    white-space: nowrap;
  }
  .contact svg { width: 22px; height: 22px; fill: var(--band-text); }

  .rule-bottom {
    position: absolute; left: 0; right: 0; top: 530px; height: 8px;
    background: var(--accent-red);
  }
</style>
</head>
<body>
  <div class="card">
    <div class="brand">
      <div class="brand-mark"></div>
      <div class="brand-name">Animal Care Oakmere Group<br>of Central PA</div>
    </div>

    <div class="rule-top"></div>

    <div class="band">
      <div class="holder">
        <div class="holder-name">Tomás R. Quintaval</div>
        <div class="holder-credentials">DVM, MLAS, BS</div>
      </div>
      <div class="band-divider"></div>
      <ul class="contact">
        <li>
          <svg viewBox="0 0 24 24" aria-hidden="true"><path d="M6.6 2.5c.6-.3 1.3-.1 1.6.5l2 3.6c.3.6.2 1.3-.3 1.7l-1.6 1.3c1 2.2 2.6 3.9 4.7 5l1.3-1.6c.4-.5 1.1-.6 1.7-.3l3.6 2c.6.3.8 1 .5 1.6l-1.2 2.4c-.4.8-1.3 1.2-2.2 1C9.7 18.4 5.6 14.3 4.3 7.6c-.2-.9.2-1.8 1-2.2z"/></svg>
          5552846017
        </li>
        <li>
          <svg viewBox="0 0 24 24" aria-hidden="true"><path d="M2 5h20v14H2z M3.5 6.5 12 13l8.5-6.5" fill="none" stroke="#f4f4f4" stroke-width="2"/><path d="M3 6l9 7 9-7v12H3z"/></svg>
          dvmtrq@mailbrook.net
        </li>
      </ul>
    </div>

    <div class="rule-bottom"></div>
  </div>
</body>
</html>
```